Business Card Design Project

Business card based on attached logo

Todd Merrick
Todd@lorvantest.com
877-514-9073 ext. 318
Www.LorvanTest.com

Industry/Entity Type

Business

```html
<!DOCTYPE html>
<html lang="en">
<head>
<meta charset="utf-8">
<title>LorvanTest – Business Card Set</title>
<link rel="stylesheet" href="https://fonts.googleapis.com/css2?family=Lato:ital,wght@0,400;0,700;0,900;1,700&display=swap">
<style>
  :root {
    --backdrop: #e7e3de;
    --label: #2b2b2b;
    --card-white: #ffffff;
    --card-grey-top: #f4f4f4;
    --card-grey-bottom: #e4e4e4;
    --red-top: #d8222a;
    --red-bottom: #a01a20;
    --brand-red: #d7242b;
    --name-red: #9a1d22;
    --ink: #111111;
    --body-text: #3a3a3a;
    --divider: #8a8a8a;
  }
  * { margin: 0; padding: 0; box-sizing: border-box; }
  html, body { width: 1200px; height: 788px; overflow: hidden; }
  body {
    background: var(--backdrop);
    font-family: "Lato", Arial, sans-serif;
    position: relative;
  }
  .side-label {
    position: absolute;
    width: 525px;
    text-align: center;
    font-size: 21px;
    color: var(--label);
    font-weight: 400;
  }
  .card {
    position: absolute;
    width: 525px;
    height: 300px;
    border-radius: 22px;
    box-shadow: 0 6px 14px rgba(0,0,0,0.22);
    overflow: hidden;
  }
  .card--front, .card--back-white { background: var(--card-white); }
  .card--back-red { background: linear-gradient(180deg, var(--red-top), var(--red-bottom)); }
  .card--back-grey { background: linear-gradient(180deg, var(--card-grey-top), var(--card-grey-bottom)); }

  .wordmark {
    position: absolute;
    display: flex;
    align-items: center;
    gap: 10px;
    font-weight: 900;
    color: var(--ink);
    letter-spacing: -0.5px;
    white-space: nowrap;
  }
  .wordmark__square {
    display: inline-block;
    background: var(--brand-red);
  }
  .card--back-red .wordmark__square { background: var(--card-white); }

  .site-url {
    position: absolute;
    left: 0; right: 0;
    text-align: center;
    font-size: 17px;
    color: var(--body-text);
  }
  .card--back-red .site-url { color: var(--card-white); }

  /* Front */
  .front-divider {
    position: absolute;
    left: 264px; top: 100px;
    width: 2px; height: 118px;
    background: linear-gradient(180deg, rgba(138,138,138,0), var(--divider) 50%, rgba(138,138,138,0));
  }
  .contact {
    position: absolute;
    left: 292px; top: 98px;
  }
  .contact__name {
    font-size: 17px;
    font-weight: 700;
    color: var(--name-red);
    margin-bottom: 13px;
  }
  .contact__row {
    font-size: 13px;
    color: var(--body-text);
    line-height: 30px;
  }
  .contact__key {
    font-weight: 700;
    font-style: italic;
    color: var(--brand-red);
    margin-right: 4px;
  }

  .raised-panel {
    position: absolute;
    left: 81px; top: 82px;
    width: 360px; height: 128px;
    background: linear-gradient(180deg, #ffffff, #f3f3f3);
    border: 1px solid #dcdcdc;
    box-shadow: 0 8px 10px -4px rgba(0,0,0,0.3);
  }
</style>
</head>
<body>

  <div class="side-label" style="left:54px; top:34px;">Front</div>
  <div class="side-label" style="left:622px; top:34px;">Back - 1</div>
  <div class="side-label" style="left:54px; top:404px;">Back - 2</div>
  <div class="side-label" style="left:622px; top:404px;">Back - 3</div>

  <!-- Front -->
  <section class="card card--front" style="left:54px; top:74px;">
    <div class="wordmark" style="left:30px; top:128px; font-size:34px;">
      <span class="wordmark__name">LorvanTest</span>
      <span class="wordmark__square" style="width:14px; height:14px;"></span>
    </div>
    <div class="front-divider"></div>
    <div class="contact">
      <p class="contact__name">Todd Merrick</p>
      <p class="contact__row"><span class="contact__key">phone</span>877-514-9073 ext. 318</p>
      <p class="contact__row"><span class="contact__key">email</span>Todd@lorvantest.com</p>
      <p class="contact__row"><span class="contact__key">web</span>www.LorvanTest.com</p>
    </div>
  </section>

  <!-- Back 1 -->
  <section class="card card--back-white" style="left:622px; top:74px;">
    <div class="wordmark" style="left:0; right:0; justify-content:center; top:92px; font-size:56px;">
      <span class="wordmark__name">LorvanTest</span>
      <span class="wordmark__square" style="width:20px; height:20px;"></span>
    </div>
    <p class="site-url" style="top:248px;">www.LorvanTest.com</p>
  </section>

  <!-- Back 2 -->
  <section class="card card--back-red" style="left:54px; top:445px;">
    <div class="wordmark" style="left:0; right:0; justify-content:center; top:92px; font-size:56px;">
      <span class="wordmark__name">LorvanTest</span>
      <span class="wordmark__square" style="width:20px; height:20px;"></span>
    </div>
    <p class="site-url" style="top:252px;">www.LorvanTest.com</p>
  </section>

  <!-- Back 3 -->
  <section class="card card--back-grey" style="left:622px; top:445px;">
    <div class="raised-panel">
      <div class="wordmark" style="left:0; right:0; justify-content:center; top:40px; font-size:38px;">
        <span class="wordmark__name">LorvanTest</span>
        <span class="wordmark__square" style="width:14px; height:14px;"></span>
      </div>
    </div>
    <p class="site-url" style="top:252px;">www.LorvanTest.com</p>
  </section>

</body>
</html>
```